Standardization and redesign of graphics for a non-fiction book

For a book project, 11 graphics need to be visually unified so that all the graphics in the book are in the same style. The graphics must be created from scratch. Just new colors aren't enough. Some of the existing graphics are by other authors who own the copyright. Accordingly, the new graphics must be truly new. This is especially true for the "2 S-curves" graphic.

Target Market(s)

Manager Furniture Industry

Industry/Entity Type

Möbel

Colors
0054AA
0677BA
7BADD7
CADEEF
E8F1F8

```html
<!DOCTYPE html>
<html lang="de">
<head>
<meta charset="utf-8">
<title>Die relevanten Megatrends in der Möbelbranche</title>
<link rel="stylesheet" href="https://fonts.googleapis.com/css2?family=Poppins:wght@400;500;600;700;800&display=swap">
<style>
  :root {
    --navy: #0054AA;
    --ocean: #0677BA;
    --sky: #7BADD7;
    --mist: #CADEEF;
    --haze: #E8F1F8;
    --ink: #34465a;
    --bg: #ffffff;
  }
  html, body { margin: 0; padding: 0; overflow: hidden; }
  body { width: 1200px; height: 1200px; background: var(--bg); font-family: "Poppins", sans-serif; }
  .canvas { position: relative; width: 1200px; height: 1200px; }
  .chart-title {
    position: absolute; top: 188px; left: 0; width: 1200px; margin: 0;
    text-align: center; font-size: 27px; line-height: 40px; font-weight: 800; color: var(--navy);
  }
  .chart-subtitle {
    position: absolute; top: 228px; left: 0; width: 1200px; margin: 0;
    text-align: center; font-size: 24px; line-height: 36px; font-weight: 400; color: var(--ocean);
  }
  .chart { position: absolute; top: 0; left: 0; }
  .band { fill: var(--haze); }
  .gridline { stroke: var(--mist); stroke-width: 1.5; stroke-dasharray: 4 4; }
  .baseline { stroke: var(--navy); stroke-width: 2; }
  .category { font-size: 15px; font-weight: 500; fill: var(--ink); text-anchor: end; }
  .value { font-size: 11.5px; font-weight: 700; }
  .value-2022 { fill: var(--navy); }
  .value-2020 { fill: var(--ocean); }
  .bar-2022 { fill: var(--navy); }
  .bar-2020 { fill: var(--sky); }
  .axis-label { font-size: 14px; font-weight: 600; fill: var(--ocean); text-anchor: middle; }
  .legend-label { font-size: 14.5px; font-weight: 600; fill: var(--ink); }
</style>
</head>
<body>
<main class="canvas">
  <h1 class="chart-title">Die relevanten Megatrends in der Möbelbranche</h1>
  <p class="chart-subtitle">Vergleich Erhebung 2020 vs 2022</p>

  <svg class="chart" width="1200" height="1200" viewBox="0 0 1200 1200" role="img" aria-label="Balkendiagramm: Megatrends 2020 und 2022 im Vergleich">
    <rect x="570" y="274" width="60" height="3" rx="1.5" fill="var(--sky)"/>

    <g class="bands">
      <rect class="band" x="150" y="293.8" width="900" height="39.4" rx="4"/>
      <rect class="band" x="150" y="372.6" width="900" height="39.4" rx="4"/>
      <rect class="band" x="150" y="451.4" width="900" height="39.4" rx="4"/>
      <rect class="band" x="150" y="530.2" width="900" height="39.4" rx="4"/>
      <rect class="band" x="150" y="609" width="900" height="39.4" rx="4"/>
      <rect class="band" x="150" y="687.8" width="900" height="39.4" rx="4"/>
      <rect class="band" x="150" y="766.6" width="900" height="39.4" rx="4"/>
      <rect class="band" x="150" y="845.4" width="900" height="39.4" rx="4"/>
      <rect class="band" x="150" y="924.2" width="900" height="39.4" rx="4"/>
    </g>

    <g class="grid">
      <line class="gridline" x1="493" y1="292" x2="493" y2="968"/>
      <line class="gridline" x1="627" y1="292" x2="627" y2="968"/>
      <line class="gridline" x1="761" y1="292" x2="761" y2="968"/>
      <line class="gridline" x1="895" y1="292" x2="895" y2="968"/>
      <line class="gridline" x1="1029" y1="292" x2="1029" y2="968"/>
    </g>

    <g class="categories">
      <text class="category" x="334" y="319">Convenience</text>
      <text class="category" x="334" y="358.4">Vertikalisierung</text>
      <text class="category" x="334" y="397.8">Biotech</text>
      <text class="category" x="334" y="437.2">Sicherheit</text>
      <text class="category" x="334" y="476.6">Industrie 4.0</text>
      <text class="category" x="334" y="516">Mobilität</text>
      <text class="category" x="334" y="555.4">Deglobalisierung</text>
      <text class="category" x="334" y="594.8">New Geo-Politics</text>
      <text class="category" x="334" y="634.2">New Work</text>
      <text class="category" x="334" y="673.6">Globalisierung</text>
      <text class="category" x="334" y="713">Gesundheit</text>
      <text class="category" x="334" y="752.4">Technologie &amp; Innovation</text>
      <text class="category" x="334" y="791.8">Urbanisierung</text>
      <text class="category" x="334" y="831.2">Individualisierung</text>
      <text class="category" x="334" y="870.6">Diversity &amp; Inclusion</text>
      <text class="category" x="334" y="910">Nachhaltigkeit</text>
      <text class="category" x="334" y="949.4">Digitalisierung</text>
    </g>

    <g class="bars-2022">
      <rect class="bar-2022" x="359" y="338.4" width="26.8" height="14" rx="3"/>
      <rect class="bar-2022" x="359" y="377.8" width="53.6" height="14" rx="3"/>
      <rect class="bar-2022" x="359" y="417.2" width="80.4" height="14" rx="3"/>
      <rect class="bar-2022" x="359" y="456.6" width="187.6" height="14" rx="3"/>
      <rect class="bar-2022" x="359" y="496" width="26.8" height="14" rx="3"/>
      <rect class="bar-2022" x="359" y="535.4" width="187.6" height="14" rx="3"/>
      <rect class="bar-2022" x="359" y="574.8" width="53.6" height="14" rx="3"/>
      <rect class="bar-2022" x="359" y="614.2" width="134" height="14" rx="3"/>
      <rect class="bar-2022" x="359" y="653.6" width="80.4" height="14" rx="3"/>
      <rect class="bar-2022" x="359" y="693" width="134" height="14" rx="3"/>
      <rect class="bar-2022" x="359" y="732.4" width="107.2" height="14" rx="3"/>
      <rect class="bar-2022" x="359" y="771.8" width="160.8" height="14" rx="3"/>
      <rect class="bar-2022" x="359" y="811.2" width="134" height="14" rx="3"/>
      <rect class="bar-2022" x="359" y="850.6" width="268" height="14" rx="3"/>
      <rect class="bar-2022" x="359" y="890" width="375.2" height="14" rx="3"/>
      <rect class="bar-2022" x="359" y="929.4" width="536" height="14" rx="3"/>
    </g>

    <g class="bars-2020">
      <rect class="bar-2020" x="359" y="315" width="26.8" height="14" rx="3"/>
      <rect class="bar-2020" x="359" y="354.4" width="26.8" height="14" rx="3"/>
      <rect class="bar-2020" x="359" y="393.8" width="53.6" height="14" rx="3"/>
      <rect class="bar-2020" x="359" y="433.2" width="53.6" height="14" rx="3"/>
      <rect class="bar-2020" x="359" y="472.6" width="80.4" height="14" rx="3"/>
      <rect class="bar-2020" x="359" y="512" width="80.4" height="14" rx="3"/>
      <rect class="bar-2020" x="359" y="551.4" width="107.2" height="14" rx="3"/>
      <rect class="bar-2020" x="359" y="590.8" width="134" height="14" rx="3"/>
      <rect class="bar-2020" x="359" y="630.2" width="160.8" height="14" rx="3"/>
      <rect class="bar-2020" x="359" y="669.6" width="160.8" height="14" rx="3"/>
      <rect class="bar-2020" x="359" y="709" width="160.8" height="14" rx="3"/>
      <rect class="bar-2020" x="359" y="748.4" width="187.6" height="14" rx="3"/>
      <rect class="bar-2020" x="359" y="787.8" width="187.6" height="14" rx="3"/>
      <rect class="bar-2020" x="359" y="827.2" width="241.2" height="14" rx="3"/>
      <rect class="bar-2020" x="359" y="866.6" width="241.2" height="14" rx="3"/>
      <rect class="bar-2020" x="359" y="906" width="375.2" height="14" rx="3"/>
      <rect class="bar-2020" x="359" y="945.4" width="428.8" height="14" rx="3"/>
    </g>

    <line class="baseline" x1="359" y1="292" x2="359" y2="968"/>

    <g class="values-2022">
      <text class="value value-2022" x="365" y="310">0%</text>
      <text class="value value-2022" x="391.8" y="349.4">1%</text>
      <text class="value value-2022" x="418.6" y="388.8">2%</text>
      <text class="value value-2022" x="445.4" y="428.2">3%</text>
      <text class="value value-2022" x="552.6" y="467.6">7%</text>
      <text class="value value-2022" x="391.8" y="507">1%</text>
      <text class="value value-2022" x="552.6" y="546.4">7%</text>
      <text class="value value-2022" x="418.6" y="585.8">2%</text>
      <text class="value value-2022" x="499" y="625.2">5%</text>
      <text class="value value-2022" x="445.4" y="664.6">3%</text>
      <text class="value value-2022" x="499" y="704">5%</text>
      <text class="value value-2022" x="472.2" y="743.4">4%</text>
      <text class="value value-2022" x="525.8" y="782.8">6%</text>
      <text class="value value-2022" x="499" y="822.2">5%</text>
      <text class="value value-2022" x="633" y="861.6">10%</text>
      <text class="value value-2022" x="740.2" y="901">14%</text>
      <text class="value value-2022" x="901" y="940.4">20%</text>
    </g>

    <g class="values-2020">
      <text class="value value-2020" x="391.8" y="326">1%</text>
      <text class="value value-2020" x="391.8" y="365.4">1%</text>
      <text class="value value-2020" x="418.6" y="404.8">2%</text>
      <text class="value value-2020" x="418.6" y="444.2">2%</text>
      <text class="value value-2020" x="445.4" y="483.6">3%</text>
      <text class="value value-2020" x="445.4" y="523">3%</text>
      <text class="value value-2020" x="472.2" y="562.4">4%</text>
      <text class="value value-2020" x="499" y="601.8">5%</text>
      <text class="value value-2020" x="525.8" y="641.2">6%</text>
      <text class="value value-2020" x="525.8" y="680.6">6%</text>
      <text class="value value-2020" x="525.8" y="720">6%</text>
      <text class="value value-2020" x="552.6" y="759.4">7%</text>
      <text class="value value-2020" x="552.6" y="798.8">7%</text>
      <text class="value value-2020" x="606.2" y="838.2">9%</text>
      <text class="value value-2020" x="606.2" y="877.6">9%</text>
      <text class="value value-2020" x="740.2" y="917">14%</text>
      <text class="value value-2020" x="793.8" y="956.4">16%</text>
    </g>

    <g class="axis">
      <text class="axis-label" x="359" y="992">0%</text>
      <text class="axis-label" x="493" y="992">5%</text>
      <text class="axis-label" x="627" y="992">10%</text>
      <text class="axis-label" x="761" y="992">15%</text>
      <text class="axis-label" x="895" y="992">20%</text>
      <text class="axis-label" x="1029" y="992">25%</text>
    </g>

    <g class="legend">
      <rect class="bar-2022" x="508" y="1016" width="22" height="14" rx="3"/>
      <text class="legend-label" x="540" y="1028">2022</text>
      <rect class="bar-2020" x="620" y="1016" width="22" height="14" rx="3"/>
      <text class="legend-label" x="652" y="1028">2020</text>
    </g>
  </svg>
</main>
</body>
</html>
```